Carpet cleaning company focused on high quality needs business cards

We are a growing company that just merged with another company and need to design a new business card. We do both residential as well as commercial cleaning. We do carpet, tile & grout, upholstery, hard floors, and stain & pet odor removal. We treat our customers like family and strive to achieve outstanding results with every job.

```html
<!DOCTYPE html>
<html lang="en">
<head>
<meta charset="utf-8">
<title>Hearthweave Cleaning – Business Card</title>
<link href="https://fonts.googleapis.com/css2?family=Montserrat:wght@400;500;700;800&display=swap" rel="stylesheet">
<style>
  :root {
    --brand-red: #e8423f;
    --ink: #1b1b1b;
    --paper: #ffffff;
    --backdrop: #e9e9ec;
    --muted: #3a3a3a;
  }
  * { box-sizing: border-box; margin: 0; padding: 0; }
  html, body { width: 1200px; height: 900px; overflow: hidden; }
  body {
    background: var(--backdrop);
    font-family: "Montserrat", Arial, sans-serif;
    color: var(--ink);
    position: relative;
  }
  .card {
    position: absolute;
    left: 340px;
    width: 520px;
    height: 300px;
    background: var(--paper);
    border-radius: 22px;
    overflow: hidden;
    box-shadow: 0 10px 30px rgba(0,0,0,0.12);
  }
  .card--front { top: 110px; }
  .card--back { top: 470px; }

  .brand { display: flex; align-items: center; gap: 14px; position: absolute; }
  .brand__mark { background: var(--brand-red); }
  .brand__name {
    font-weight: 800;
    color: var(--ink);
    line-height: 1.02;
    text-transform: uppercase;
    letter-spacing: 0.5px;
  }
  .card--front .brand { left: 110px; top: 100px; }
  .card--front .brand__mark { width: 96px; height: 96px; }
  .card--front .brand__name { font-size: 34px; }

  .card--back .brand { left: 30px; top: 30px; gap: 10px; }
  .card--back .brand__mark { width: 48px; height: 48px; }
  .card--back .brand__name { font-size: 17px; }

  .card__decor { position: absolute; inset: 0; }

  .person { position: absolute; left: 30px; top: 110px; }
  .person__name { color: var(--brand-red); font-weight: 700; font-size: 26px; }
  .person__title { font-size: 13px; font-weight: 500; margin-top: 2px; }

  .contact-list { position: absolute; left: 30px; top: 178px; list-style: none; }
  .contact-list li {
    display: flex; align-items: center; gap: 10px;
    font-size: 12.5px; font-weight: 500; color: var(--muted);
    height: 19px;
  }
  .contact-list svg { width: 12px; height: 12px; fill: var(--brand-red); }

  .address {
    position: absolute; right: 30px; top: 160px;
    font-size: 12px; font-weight: 500; line-height: 1.35; text-align: left;
  }
  .web-band {
    position: absolute; right: 22px; bottom: 17px;
    color: var(--paper); font-size: 12px; font-weight: 500;
  }
</style>
</head>
<body>

<section class="card card--front" aria-label="Card front">
  <div class="brand">
    <div class="brand__mark"></div>
    <div class="brand__name">Hearthweave<br>Cleaning</div>
  </div>
</section>

<section class="card card--back" aria-label="Card back">
  <svg class="card__decor" viewBox="0 0 520 300" width="520" height="300" aria-hidden="true">
    <line x1="30" y1="168" x2="490" y2="100" stroke="#e8423f" stroke-width="1"/>
    <polygon points="92,300 116,300 346,262 342,256" fill="#1b1b1b"/>
    <polygon points="130,300 520,300 520,244 366,244 352,262" fill="#e8423f"/>
  </svg>

  <div class="brand">
    <div class="brand__mark"></div>
    <div class="brand__name">Hearthweave<br>Cleaning</div>
  </div>

  <div class="person">
    <div class="person__name">Daniel Reyes</div>
    <div class="person__title">CEO</div>
  </div>

  <ul class="contact-list">
    <li><svg viewBox="0 0 24 24"><path d="M6.6 10.8a15 15 0 0 0 6.6 6.6l2.2-2.2c.3-.3.7-.4 1-.2 1.1.4 2.3.6 3.6.6.6 0 1 .4 1 1V20c0 .6-.4 1-1 1A17 17 0 0 1 3 4c0-.6.4-1 1-1h3.5c.6 0 1 .4 1 1 0 1.3.2 2.5.6 3.6.1.3 0 .7-.2 1z"/></svg>555 018-2740</li>
    <li><svg viewBox="0 0 24 24"><path d="M7 1h10a2 2 0 0 1 2 2v18a2 2 0 0 1-2 2H7a2 2 0 0 1-2-2V3a2 2 0 0 1 2-2zm0 3v14h10V4zm5 15.5a1 1 0 1 0 0 2 1 1 0 0 0 0-2z"/></svg>555 018-2740</li>
    <li><svg viewBox="0 0 24 24"><path d="M2 5h20v14H2zm2 2v.5l8 5 8-5V7z"/></svg>info@hearthweaveclean.com</li>
    <li><svg viewBox="0 0 24 24"><circle cx="12" cy="12" r="10"/></svg>www.hearthweaveclean.com</li>
  </ul>

  <div class="address">418 Linden Grove Ave, #112<br>Fairmont, OH 43210</div>

  <div class="web-band">www.hearthweaveclean.com</div>
</section>

</body>
</html>
```